Family business needs stationery redesign with new logo

Family owned company, established in 1987 wanting a brand 'refresh'. We are an electrical, refrigeration and construction company based in the Barkly Region Northern Territory, Australia. We have a new logo we would like to use which is uploaded along with our current letterhead and email signature. We are also dropping the word 'contractors' so please do not include this on any designs. Please note also, the 'orange' color used in our logo and designs should be Northern Territory red ochre which is as follows:

RGB (Hex): #C75B12
PantoneĀ® 159 C
CMYK: 1 / 74 / 100 / 7

We are needing our stationery redesigned using our new logo. Please include letterheads, business cards, envelopes, and email signatures.

We currently use our business letterheads for quotations, invoices, letters, HR matters, and internal memos.

We also need a separate simplified letterhead for internal paperwork such as employee leave forms, meeting agendas, and meeting minutes etc.

Reason: Needing more submissions of full package designs. We are wanting all our stationery, including business cards, letterheads, email signatures, envelopes, etc to be cohesive. We also require ALL the information, as supplied on our template letterhead, to be included on the new letterhead designs. including electrical license no.etc Thank you, R&W

Reason: needing more time as work has got in the way of looking over designs. A lot of designs not meeting the brief/criteria.

Industry/Entity Type

Business

Colors
0355a3
f37122

Requirements
Must have
• The 'orange' color used in the designs should be Northern Territory red ochre which is as follows:
• RGB (Hex): #C75B12
• PantoneĀ® 159 C
• CMYK: 1 / 74 / 100 / 7
• ***MUST INCLUDE ALL INFORMATION THAT IS ON OUR CURRENT LETTERHEAD***
Should not have
• Please do not include the word 'contractors'

```html
<!DOCTYPE html>
<html lang="en">
<head>
<meta charset="utf-8">
<title>R&amp;W Stationery Set</title>
<link href="https://fonts.googleapis.com/css2?family=Source+Sans+3:wght@400;600;700&display=swap" rel="stylesheet">
<style>
:root{
  --navy:#253670;
  --ochre:#C75B12;
  --paper:#ffffff;
  --ink:#5a5a5a;
  --backdrop:#2b2b2b;
}
*{margin:0;padding:0;box-sizing:border-box}
html,body{width:1200px;height:922px;overflow:hidden;background:var(--backdrop)}
body{position:relative;font-family:"Source Sans 3",Arial,sans-serif;color:var(--ink)}
.sheet{position:absolute;background:var(--paper);box-shadow:0 2px 8px rgba(0,0,0,.5)}
.wordmark{font-weight:700;color:var(--navy);line-height:1;white-space:nowrap}
.wordmark.on-navy{color:#fff}
.band{position:absolute;left:0;right:0;bottom:0;background:var(--navy);border-top:2px solid var(--ochre);box-shadow:0 -2px 0 #fff inset}
.band-text{display:flex;justify-content:space-between;align-items:center;height:100%;padding:0 32px;color:#fff;font-size:8.5px}
.dot{color:var(--ochre)}
.contact-list{list-style:none}
.contact-list li{display:flex;align-items:center;gap:3px}
.icon{width:6px;height:6px;flex:none}
.name{color:var(--navy);font-weight:700}

/* letterhead */
.letterhead{left:21px;top:190px;width:549px;height:711px}
.letterhead .wordmark{position:absolute;left:0;right:0;top:236px;text-align:center;font-size:40px;top:40px}
.lh-footer{position:absolute;left:32px;right:32px;top:648px;display:flex;font-size:7.8px;line-height:10.5px}
.lh-footer .col{flex:1}
.lh-footer .mid{text-align:center;border-left:1px solid var(--navy);border-right:1px solid var(--navy);flex:0 0 136px}
.lh-footer .right{text-align:right}
.lh-footer b{color:var(--navy)}
.letterhead .band{height:24px}

/* wide business card */
.card-wide{left:607px;top:21px;width:358px;height:141px}
.card-wide .info{position:absolute;left:19px;top:21px;font-size:6.5px;line-height:9px}
.card-wide .name{font-size:10px;line-height:11px}
.card-wide .gap{margin-top:6px}
.card-wide .wordmark{position:absolute;right:28px;top:31px;font-size:24px}
.card-wide .band{height:6px}

/* small card front & back */
.card-front{left:607px;top:190px;width:226px;height:128px;border-radius:6px;overflow:hidden}
.card-front .wordmark{position:absolute;left:24px;top:54px;font-size:19px}
.card-front .rule{position:absolute;left:87px;top:26px;width:1px;height:78px;background:var(--navy)}
.card-front .info{position:absolute;left:96px;top:25px;font-size:5px;line-height:7.3px}
.card-front .name{font-size:8px;line-height:9px}
.card-front .gap{margin-top:4px}
.card-front .band{height:6px}
.card-back{left:847px;top:190px;width:226px;height:128px;border-radius:6px;background:var(--navy)}
.card-back .wordmark{position:absolute;left:0;right:0;top:48px;text-align:center;font-size:28px}
.card-back .tag{position:absolute;left:0;right:0;top:111px;text-align:center;color:#fff;font-size:5.6px}

/* envelope back */
.env-back{left:607px;top:365px;width:574px;height:251px}
.env-back svg{position:absolute;left:0;top:0}
.env-back .wordmark{position:absolute;left:0;right:0;top:27px;text-align:center;font-size:20px}

/* envelope front */
.env-front{left:607px;top:650px;width:574px;height:251px}
.env-front .wordmark{position:absolute;left:26px;top:29px;font-size:32px}
.env-front .addr{position:absolute;left:25px;top:79px;font-size:8.2px;line-height:10.5px}
.env-front .band{height:24px}
</style>
</head>
<body>

<!-- Letterhead -->
<section class="sheet letterhead" aria-label="Letterhead">
  <div class="wordmark">R&amp;W</div>
  <footer class="lh-footer">
    <ul class="col contact-list">
      <li><svg class="icon" viewBox="0 0 6 6"><path d="M1 5 Q1 1 5 1" stroke="#C75B12" stroke-width="1.6" fill="none"/></svg>08 8900 1234</li>
      <li><svg class="icon" viewBox="0 0 6 6"><rect x="0.5" y="1.5" width="5" height="4" rx="1" fill="#C75B12"/></svg>08 8900 5678</li>
      <li><svg class="icon" viewBox="0 0 6 6"><rect x="0.3" y="1.2" width="5.4" height="3.6" fill="#C75B12"/></svg>danawhitfield@rwservices.com.au</li>
    </ul>
    <div class="col mid">PO Box 4410<br>52 Ridge St<br>Barkly Creek NT 0870</div>
    <div class="col right"><b>ABN</b> 12 345 678 901<br>Refrigerant Trading Authorisation AU09981<br>NT Electrical Contractors License 09876</div>
  </footer>
  <div class="band"><div class="band-text"><span>www.rwservices.com.au</span><span>Electrical <span class="dot">•</span> Refrigeration <span class="dot">•</span> Building Services</span></div></div>
</section>

<!-- Wide business card -->
<section class="sheet card-wide" aria-label="Business card">
  <div class="info">
    <div class="name">Dana Whitfield</div>
    <div>Corporate Services Manager, R&amp;W</div>
    <div class="gap">PO Box 4410, 52 Ridge St<br>Barkly Creek NT 0870</div>
    <ul class="contact-list gap">
      <li><svg class="icon" viewBox="0 0 6 6"><path d="M1 5 Q1 1 5 1" stroke="#C75B12" stroke-width="1.6" fill="none"/></svg>08 8900 1234</li>
      <li><svg class="icon" viewBox="0 0 6 6"><rect x="1.5" y="0.3" width="3" height="5.4" rx=".6" fill="none" stroke="#C75B12"/></svg>0400 555 019</li>
      <li><svg class="icon" viewBox="0 0 6 6"><rect x="0.5" y="1.5" width="5" height="4" rx="1" fill="#C75B12"/></svg>08 8900 5678</li>
      <li><svg class="icon" viewBox="0 0 6 6"><rect x="0.3" y="1.2" width="5.4" height="3.6" fill="#C75B12"/></svg>danawhitfield@rwservices.com.au</li>
      <li><svg class="icon" viewBox="0 0 6 6"><circle cx="3" cy="3" r="2.7" fill="#C75B12"/></svg>www.rwservices.com.au</li>
    </ul>
  </div>
  <div class="wordmark">R&amp;W</div>
  <div class="band"></div>
</section>

<!-- Small card front -->
<section class="sheet card-front" aria-label="Business card front">
  <div class="wordmark">R&amp;W</div>
  <div class="rule"></div>
  <div class="info">
    <div class="name">Dana Whitfield</div>
    <div>Corporate Services Manager, R&amp;W</div>
    <div class="gap">PO Box 4410, 52 Ridge St<br>Barkly Creek NT 0870</div>
    <ul class="contact-list gap">
      <li><svg class="icon" viewBox="0 0 6 6"><path d="M1 5 Q1 1 5 1" stroke="#C75B12" stroke-width="1.6" fill="none"/></svg>08 8900 1234</li>
      <li><svg class="icon" viewBox="0 0 6 6"><rect x="1.5" y="0.3" width="3" height="5.4" rx=".6" fill="none" stroke="#C75B12"/></svg>0400 555 019</li>
      <li><svg class="icon" viewBox="0 0 6 6"><rect x="0.5" y="1.5" width="5" height="4" rx="1" fill="#C75B12"/></svg>08 8900 5678</li>
      <li><svg class="icon" viewBox="0 0 6 6"><rect x="0.3" y="1.2" width="5.4" height="3.6" fill="#C75B12"/></svg>danawhitfield@rwservices.com.au</li>
      <li><svg class="icon" viewBox="0 0 6 6"><circle cx="3" cy="3" r="2.7" fill="#C75B12"/></svg>www.rwservices.com.au</li>
    </ul>
  </div>
  <div class="band"></div>
</section>

<!-- Small card back -->
<section class="sheet card-back" aria-label="Business card back">
  <div class="wordmark on-navy">R&amp;W</div>
  <div class="tag">Electrical <span class="dot">•</span> Refrigeration <span class="dot">•</span> Building Services</div>
</section>

<!-- Envelope back -->
<section class="sheet env-back" aria-label="Envelope back">
  <svg width="574" height="74" viewBox="0 0 574 74">
    <path d="M0 0 H574 L565 60 Q563 74 548 74 H26 Q11 74 9 60 Z" fill="#253670"/>
  </svg>
  <div class="wordmark on-navy">R&amp;W</div>
</section>

<!-- Envelope front -->
<section class="sheet env-front" aria-label="Envelope front">
  <div class="wordmark">R&amp;W</div>
  <div class="addr">PO Box 4410, 52 Ridge St<br>Barkly Creek NT 0870</div>
  <div class="band"><div class="band-text"><span>www.rwservices.com.au</span><span>Electrical <span class="dot">•</span> Refrigeration <span class="dot">•</span> Building Services</span></div></div>
</section>

</body>
</html>
```